New business card for a regional office of a US M&A company

We need business card for a finance company, office based in Hong Kong , our Head office is in US, our business is to Merge and acquires companies , the new office will be a regional office for the Asia Pacific region. We want to use the head office logo as attached ( but don't have to be exactly the same, can be a variation to it) as a base and then add Asia Pacific alongside the logo.
We would prefer to have be bilingual Eng + Chinese, although we don't really have Chinese company name .

Industry/Entity Type

Business

Contact Information for Business Card

Clara Jo Tsang
 

VP,
APAC M&A Operations
Orin Vantage Asia Pacific Limited
 
Unit 1407, K18
18 Tai Lok Shan Road, 
Hong Kong 
 
M: +852 6038 1742
T : +852 2836 4100
F : +852 2836 4177
VOIP: 4158
 
cjtsang@orinvantage.com

Font styles to use
Serif
Sans Serif

Colors

Designer to choose colors to be used in the design.

Requirements
Must have
• APAC Office

```html
<!DOCTYPE html>
<html lang="en">
<head>
<meta charset="utf-8">
<title>Orin Vantage Asia Pacific – Business Card</title>
<link rel="stylesheet" href="https://fonts.googleapis.com/css2?family=Open+Sans:wght@400;600;700&family=Tinos&display=swap">
<style>
  :root {
    --navy: #0f2a4a;
    --cyan: #1ba3d8;
    --ink: #3a3d42;
    --paper: #f6f7f8;
    --paper-back: #eff0f2;
    --rule: #9aa0a6;
    --map: #dfe2e6;
    --stage: #d9dbde;
  }
  * { box-sizing: border-box; margin: 0; padding: 0; }
  html, body { width: 1200px; height: 834px; overflow: hidden; }
  body {
    background: var(--stage);
    font-family: "Open Sans", Arial, sans-serif;
    color: var(--ink);
    display: flex;
    align-items: center;
    justify-content: center;
    gap: 40px;
  }
  .card {
    position: relative;
    width: 540px;
    height: 309px;
    overflow: hidden;
    box-shadow: 0 6px 18px rgba(0,0,0,.18);
  }

  /* Logo lockup */
  .logo-box {
    position: absolute;
    width: 172px;
    height: 100px;
    background: var(--navy);
    border-bottom: 3px solid var(--cyan);
    display: flex;
    flex-direction: column;
    align-items: center;
    justify-content: center;
    gap: 10px;
  }
  .logo-square {
    width: 26px; height: 26px;
    border: 3px solid #e9edf2;
  }
  .logo-name {
    font-weight: 700;
    font-size: 17px;
    letter-spacing: .5px;
    color: var(--cyan);
    white-space: nowrap;
  }

  /* Back side */
  .card-back { background: var(--paper-back); }
  .back-tab {
    position: absolute;
    left: 300px; top: 0;
    width: 122px; height: 14px;
    background: var(--navy);
    border-bottom: 3px solid var(--cyan);
  }
  .world-map {
    position: absolute;
    left: 20px; top: 40px;
    width: 470px; height: 240px;
    background: radial-gradient(ellipse at 50% 50%, var(--map) 0%, rgba(223,226,230,.4) 60%, rgba(239,240,242,0) 80%);
  }
  .card-back .logo-box { right: 0; top: 168px; }

  /* Front side */
  .card-front { background: var(--paper); }
  .card-front .logo-box { right: 40px; top: 26px; }
  .name-rule {
    position: absolute;
    left: 220px; right: 40px; top: 146px;
    border-top: 1px solid var(--rule);
  }
  .person {
    position: absolute;
    left: 40px; top: 158px;
  }
  .person-name {
    font-family: "Tinos", "Times New Roman", serif;
    font-size: 19px;
    color: var(--ink);
  }
  .person-title {
    font-size: 12.5px;
    color: var(--cyan);
    margin-top: 2px;
  }
  .contacts {
    position: absolute;
    right: 40px; top: 156px;
    list-style: none;
    font-size: 11.5px;
    line-height: 16px;
    text-align: right;
  }
  .contacts li { display: flex; justify-content: flex-end; align-items: center; gap: 6px; }
  .contacts svg { width: 9px; height: 9px; fill: none; stroke: var(--cyan); stroke-width: 1.4; }
  .contacts .no-icon { padding-right: 15px; }
  .address-rule {
    position: absolute;
    left: 40px; width: 200px; top: 212px;
    border-top: 1px solid var(--rule);
  }
  .address {
    position: absolute;
    left: 40px; top: 218px;
    font-style: normal;
    font-size: 11.5px;
    line-height: 14.5px;
  }
  .address .company { color: var(--cyan); font-weight: 600; }
  .bottom-band {
    position: absolute;
    left: 0; right: 0; bottom: 0;
    height: 16px;
    background: var(--navy);
    border-top: 3px solid var(--cyan);
  }
</style>
</head>
<body>

  <section class="card card-back" aria-label="Card back">
    <div class="back-tab"></div>
    <div class="world-map" role="img" aria-label="Faint dotted world map background"></div>
    <div class="logo-box">
      <div class="logo-square"></div>
      <div class="logo-name">ORIN VANTAGE</div>
    </div>
  </section>

  <section class="card card-front" aria-label="Card front">
    <div class="logo-box">
      <div class="logo-square"></div>
      <div class="logo-name">ORIN VANTAGE</div>
    </div>

    <div class="name-rule"></div>
    <div class="person">
      <p class="person-name">Clara Jo Tsang</p>
      <p class="person-title">VP, APAC M&amp;A Operations</p>
    </div>

    <ul class="contacts">
      <li>+852 6038 1742
        <svg viewBox="0 0 10 10"><rect x="2.5" y="0.8" width="5" height="8.4" rx="1"/></svg></li>
      <li>+852 2836 4100
        <svg viewBox="0 0 10 10"><path d="M2 1.5 L4 1.5 L4.6 3.6 L3.5 4.6 Q4.6 6.4 5.9 6.5 L7 5.4 L8.8 6 L8.8 8 Q4 8.8 1.5 2.5 Z"/></svg></li>
      <li>+852 2836 4177
        <svg viewBox="0 0 10 10"><rect x="1" y="4" width="8" height="4.5"/><rect x="2.8" y="1" width="4.4" height="3"/></svg></li>
      <li class="no-icon">VOIP 4158</li>
    </ul>

    <div class="address-rule"></div>
    <address class="address">
      <span class="company">Orin Vantage Asia Pacific Limited</span><br>
      Unit 1407, K18<br>
      18 Tai Lok Shan Road,<br>
      Hong Kong
    </address>

    <div class="bottom-band"></div>
  </section>

</body>
</html>
```